Roofing Company Modern look

I want a modern and sophisticated look for our roofing business.

Our address is :

5217 Mallow Creek Ln
Orlando, Fl 32825

(407)-583-2196

www.HarborlineRoofsFl.com

I also want to make sure on the back there is a spot to put
Project Manager Name :

Number:

Because the cards will be used by all sales people

Project Manager Name :

Also there are accreditation we have logos are uploaded here as well that I would like maybe on the back of card as well

I also want to highlight our special attributions or trades:

Residential & Commercial
Fully Insured
License # CCC7482913
Insurance Claims
Serving Central Florida Since 1992
Free Estimates

Contact Information for Business Card

Our address is :

5217 Mallow Creek Ln
Orlando, Fl 32825

(407)-583-2196

Project Manager Name :

Residential & Commercial
Fully Insured
License # CCC7482913
Insurance Claims
Free Estimates

Font styles to use
Serif
Sans Serif

Colors
3176b5

Requirements
Must have
• Must have royal blue like my logo grey and black are the colors I like

```html
<!DOCTYPE html>
<html lang="en">
<head>
<meta charset="utf-8">
<title>Harborline Roofing &amp; Gutters – Business Card</title>
<link rel="stylesheet" href="https://fonts.googleapis.com/css2?family=Michroma&family=Didact+Gothic&display=swap">
<style>
  :root {
    --page: #2b2b2c;
    --card: #141415;
    --blue: #2f8fe0;
    --royal: #3176b5;
    --grey: #a9abae;
    --light: #d9dadc;
    --rule: #3a3b3d;
    --badge-silver: #c9ccd0;
    --badge-navy: #1f4f8f;
    --badge-red: #d8262c;
  }
  * { margin: 0; padding: 0; box-sizing: border-box; }
  html, body { width: 1200px; height: 866px; overflow: hidden; }
  body {
    background: var(--page);
    font-family: "Didact Gothic", "Century Gothic", sans-serif;
    display: flex; flex-direction: column; align-items: center; justify-content: center;
    gap: 30px;
  }
  .card {
    position: relative;
    width: 700px; height: 400px;
    background: var(--card);
    box-shadow: 0 14px 30px rgba(0,0,0,.55);
    overflow: hidden;
  }
  .brand {
    position: absolute;
    display: flex; align-items: center; gap: 16px;
    font-family: "Michroma", sans-serif;
    color: var(--blue);
  }
  .brand__mark { width: 46px; height: 46px; border-radius: 50%; background: var(--royal); flex: none; }
  .brand__name { font-size: 30px; line-height: 1; letter-spacing: 2px; }
  .brand__sub { font-size: 11.5px; letter-spacing: 2px; margin-top: 6px; }

  /* front */
  .front .brand { top: 70px; left: 250px; }
  .person-row {
    position: absolute; left: 54px; right: 54px; top: 186px;
    display: flex; align-items: flex-end; gap: 18px;
  }
  .person {
    font-family: "Michroma", sans-serif;
    color: var(--blue); font-size: 22px; line-height: 1.2; letter-spacing: 2px;
    white-space: nowrap; flex: none;
  }
  .divider { flex: 1; height: 1px; background: var(--rule); margin-bottom: 5px; }
  .contact { position: absolute; left: 54px; top: 236px; list-style: none; color: var(--light); font-size: 19px; }
  .contact li { display: flex; align-items: center; gap: 10px; margin-bottom: 6px; }
  .contact svg { width: 16px; height: 16px; flex: none; }
  .address {
    position: absolute; right: 54px; bottom: 44px; text-align: right; font-style: normal;
    color: var(--grey); font-size: 22px; line-height: 1.25; letter-spacing: 1px;
  }

  /* back */
  .services { position: absolute; left: 50px; top: 44px; list-style: none; color: var(--light); font-size: 19px; letter-spacing: 1px; }
  .services li { display: flex; align-items: center; gap: 12px; margin-bottom: 5px; }
  .services li::before { content: ""; width: 8px; height: 8px; border-radius: 50%; background: var(--blue); flex: none; }
  .back .brand { left: 50px; bottom: 50px; }
  .back .brand__name { font-size: 24px; }
  .back .brand__sub { font-size: 9.5px; }
  .back .brand__mark { width: 38px; height: 38px; }
  .badge { position: absolute; }
  .badge--listing { right: 40px; top: 150px; width: 80px; height: 80px; border-radius: 50%; background: var(--badge-silver); border: 6px solid #8d9196; }
  .badge--applicator { right: 46px; top: 245px; width: 70px; height: 52px; background: var(--badge-navy); clip-path: polygon(15% 0,85% 0,100% 50%,85% 100%,15% 100%,0 50%); }
  .badge--contractor { right: 140px; top: 300px; width: 120px; height: 48px; background: var(--badge-red); border: 4px solid #fff; }
  .badge--accredited { right: 60px; top: 310px; width: 64px; height: 72px; background: var(--badge-navy); border: 4px solid #fff; border-radius: 6px; }
</style>
</head>
<body>
  <section class="card front" aria-label="Card front">
    <div class="brand">
      <span class="brand__mark"></span>
      <div>
        <div class="brand__name">HARBORLINE</div>
        <div class="brand__sub">ROOFING &amp; GUTTERS LLC</div>
      </div>
    </div>
    <div class="person-row">
      <div class="person">MARCUS DELANEY</div>
      <div class="divider"></div>
    </div>
    <ul class="contact">
      <li>
        <svg viewBox="0 0 16 16"><path d="M4 1.5l2.2 2.6-1.3 1.7a8 8 0 0 0 5.3 5.3l1.7-1.3 2.6 2.2-1.6 2.3C7.4 14.3 1.7 8.6 1.7 3.1z" fill="none" stroke="var(--blue)" stroke-width="1.5"/></svg>
        (407)-583-2196
      </li>
      <li>
        <svg viewBox="0 0 16 16"><circle cx="8" cy="8" r="6.5" fill="none" stroke="var(--blue)" stroke-width="1.4"/><path d="M1.5 8h13M8 1.5c-3 3.5-3 9.5 0 13M8 1.5c3 3.5 3 9.5 0 13" fill="none" stroke="var(--blue)" stroke-width="1.2"/></svg>
        www.HarborlineRoofsFl.com
      </li>
    </ul>
    <address class="address">5217 Mallow Creek Ln<br>Orlando, Fl 32825</address>
  </section>

  <section class="card back" aria-label="Card back">
    <ul class="services">
      <li>RESIDENTIAL &amp; COMMERCIAL</li>
      <li>LICENSE # CCC7482913</li>
      <li>SERVING CENTRAL FLORIDA SINCE 1992</li>
      <li>FREE ESTIMATES</li>
      <li>FULLY INSURED</li>
      <li>INSURANCE CLAIMS</li>
    </ul>
    <div class="brand">
      <span class="brand__mark"></span>
      <div>
        <div class="brand__name">HARBORLINE</div>
        <div class="brand__sub">ROOFING &amp; GUTTERS LLC</div>
      </div>
    </div>
    <div class="badge badge--listing" role="img" aria-label="Listing approval badge"></div>
    <div class="badge badge--applicator" role="img" aria-label="Shingle applicator certification badge"></div>
    <div class="badge badge--contractor" role="img" aria-label="Authorized roofing contractor badge"></div>
    <div class="badge badge--accredited" role="img" aria-label="Accredited business badge"></div>
  </section>
</body>
</html>
```